Silver Bloom Marisol's Cleaning Service Business Cards Project

A business card with all contact details with logo design on there (already have a logo) eye catching Logo and contact info on one side, full logo on the back, must target upper class residential and corporate companies, fitness companies, still keep it on the feminine side of things , must look elegant

Target Market(s)

Upper class homes and corporate companies

Industry/Entity Type

Cleaning Service

Contact Information for Business Card

Name: Marisol Quenby
Position: Director
ABN: 31647209853
Email: marisolssilvercleaning@tidymail.example
Number: 0417906354

Font styles to use
Decorative

Colors

Designer to choose colors to be used in the design.

Requirements
Must have
• Available Sydney Wide, contact info and logo on one side, full logo on the back
Nice to have
• Professional appearance
Should not have
• Cheap advert looking stuff

```html
<!DOCTYPE html>
<html lang="en">
<head>
<meta charset="utf-8">
<title>Silver Bloom – Business Cards</title>
<link rel="stylesheet" href="https://fonts.googleapis.com/css2?family=Roboto:wght@400;500&family=Lora:wght@600&display=swap">
<style>
  :root {
    --backdrop: #e4e4e4;
    --card-dark: #2e323f;
    --aqua: #31e5dc;
    --ink: #111418;
    --white: #ffffff;
    --rule: #c9cbd1;
  }
  * { box-sizing: border-box; margin: 0; padding: 0; }
  html, body { width: 1200px; height: 960px; overflow: hidden; }
  body { background: var(--backdrop); font-family: "Roboto", Arial, sans-serif; position: relative; }

  .card { position: absolute; width: 600px; height: 343px; border-radius: 18px; overflow: hidden; }

  .brand { position: absolute; text-align: center; font-family: "Lora", Georgia, serif; font-weight: 600; }
  .brand-mark { display: block; margin: 0 auto; border-radius: 50%; background: currentColor; }
  .brand-name { text-transform: uppercase; white-space: nowrap; }
  .brand-tagline { text-transform: uppercase; white-space: nowrap; }

  /* Front */
  .card-front { left: 314px; top: 113px; background: var(--card-dark); }
  .card-front .brand { left: 366px; width: 200px; top: 35px; color: var(--aqua); }
  .card-front .brand-mark { width: 62px; height: 62px; }
  .card-front .brand-name { margin-top: 48px; font-size: 19px; letter-spacing: 0.4px; line-height: 24px; }
  .card-front .brand-tagline { margin-top: 3px; font-size: 7.5px; letter-spacing: 2px; }

  .holder { position: absolute; left: 39px; top: 183px; color: var(--aqua); }
  .holder-name { font-size: 20px; font-weight: 500; letter-spacing: 0.2px; text-transform: uppercase; }
  .holder-role { font-size: 14px; font-weight: 500; margin-top: 2px; text-transform: uppercase; }

  .divider { position: absolute; left: 39px; right: 38px; top: 237px; height: 1px; background: var(--rule); }

  .contacts { position: absolute; left: 37px; top: 250px; list-style: none; color: var(--white); font-size: 14px; }
  .contacts li { display: flex; align-items: center; height: 19px; }
  .contacts svg { width: 13px; height: 13px; margin-right: 9px; fill: var(--aqua); flex: none; }

  .abn { position: absolute; right: 36px; top: 286px; color: var(--white); font-size: 14px; }

  .front-band { position: absolute; left: 0; right: 0; bottom: 0; height: 16px; background: var(--aqua); border-top: 2px solid var(--white); }

  /* Back */
  .card-back { left: 312px; top: 472px; background: var(--aqua); }
  .card-back .brand { left: 0; right: 0; top: 80px; color: var(--ink); }
  .card-back .brand-mark { width: 74px; height: 74px; }
  .card-back .brand-name { margin-top: 58px; font-size: 24px; letter-spacing: 0.5px; line-height: 30px; }
  .card-back .brand-tagline { margin-top: 3px; font-size: 9px; letter-spacing: 2.6px; }
  .web { position: absolute; left: 0; right: 0; top: 292px; text-align: center; font-size: 14px; letter-spacing: 3px; color: var(--ink); }
</style>
</head>
<body>
  <section class="card card-front">
    <div class="brand">
      <span class="brand-mark"></span>
      <div class="brand-name">Silver Bloom</div>
      <div class="brand-tagline">Marisol's Cleaning Service</div>
    </div>

    <div class="holder">
      <div class="holder-name">Marisol Quenby</div>
      <div class="holder-role">Director</div>
    </div>

    <div class="divider"></div>

    <ul class="contacts">
      <li><svg viewBox="0 0 24 24"><path d="M6.6 10.8a15.1 15.1 0 0 0 6.6 6.6l2.2-2.2c.3-.3.7-.4 1-.2 1.1.4 2.3.6 3.6.6.6 0 1 .4 1 1V20c0 .6-.4 1-1 1C10.6 21 3 13.4 3 4c0-.6.4-1 1-1h3.5c.6 0 1 .4 1 1 0 1.3.2 2.5.6 3.6.1.3 0 .7-.2 1z"/></svg>0417906354</li>
      <li><svg viewBox="0 0 24 24"><path d="M2 5h20v14H2z"/><path d="M2 5l10 7 10-7" fill="none" stroke="#2e323f" stroke-width="2"/></svg>marisolssilvercleaning@tidymail.example</li>
      <li><svg viewBox="0 0 24 24"><circle cx="12" cy="12" r="10"/><path d="M2 12h20M12 2c3 3 3 17 0 20M12 2c-3 3-3 17 0 20" fill="none" stroke="#2e323f" stroke-width="1.5"/></svg>www.silverbloomcleaning.example</li>
    </ul>

    <div class="abn">ABN: 31647209853</div>
    <div class="front-band"></div>
  </section>

  <section class="card card-back">
    <div class="brand">
      <span class="brand-mark"></span>
      <div class="brand-name">Silver Bloom</div>
      <div class="brand-tagline">Marisol's Cleaning Service</div>
    </div>
    <div class="web">www.silverbloomcleaning.example</div>
  </section>
</body>
</html>
```